Tolvar Air and Electrical Website

Simple and easy to use website for a Electrical and Air Conditioning contracting business.Use stock photosOnline contact portallogo still to be supplied

Target Market(s)

Mums and Dads who want a local contractor

Coding

Coded - Design and coding required

Number of Pages Required

2 page

Font styles to use
Sans Serif

Colors
f04a50
3276b5
33a6d7

Requirements
Must have
• Simple and easy to use
• Ph number
• 4 web address; linked to page
• 0417385926
• tolvar.com.au
• tolvarelectrical.com.au
• tolvarairandelectrical.com.au
• tolvarair.com.au
Nice to have
• Split System Air Con Picture
• Electrical Pictures

```html
<!DOCTYPE html>
<html lang="en">
<head>
<meta charset="utf-8">
<title>Tolvar Air and Electrical</title>
<link href="https://fonts.googleapis.com/css2?family=Montserrat:wght@300;400;600;700&family=Roboto:wght@300;400;500;700&family=Nunito+Sans:wght@400;600;700&display=swap" rel="stylesheet">
<style>
:root{
  --red:#f04a50;
  --red-deep:#e8323a;
  --blue:#3276b5;
  --blue-mid:#2f63ad;
  --sky:#33a6d7;
  --navy:#233a7a;
  --ink:#1d1d1f;
  --black:#161616;
  --text:#4a4a4a;
  --light:#eef0f3;
  --white:#ffffff;
}
*{margin:0;padding:0;box-sizing:border-box}
html,body{width:1200px;height:4754px;overflow:hidden}
body{position:relative;background:var(--white);font-family:"Roboto",sans-serif;color:var(--text)}
.abs{position:absolute}
a{color:inherit;text-decoration:none}

/* hero */
.hero{left:0;top:0;width:1200px;height:770px;background:linear-gradient(120deg,#8a8f93 0%,#b9bcbd 30%,#4c5b78 60%,#2b3656 100%);clip-path:polygon(0 0,1200px 0,1200px 600px,600px 766px,0 600px)}
.hero-shade{left:0;top:0;width:1200px;height:770px;background:rgba(15,20,35,.35);clip-path:polygon(0 0,1200px 0,1200px 600px,600px 766px,0 600px)}
.hero-edge{left:0;top:596px}
.logo{left:142px;top:46px;font-family:"Montserrat",sans-serif;font-size:44px;font-weight:400;color:var(--white);letter-spacing:.5px}
.nav{left:561px;top:68px;display:flex;gap:31px;font-family:"Roboto",sans-serif;font-weight:700;font-size:15px;color:var(--white);letter-spacing:.3px}
.hero-title{left:0;width:1200px;top:292px;text-align:center;color:var(--white);font-family:"Montserrat",sans-serif}
.hero-title .l1{font-size:50px;font-weight:700;line-height:62px;text-shadow:0 2px 6px rgba(0,0,0,.35)}
.hero-title .l2{font-size:50px;font-weight:300;line-height:62px;text-shadow:0 2px 6px rgba(0,0,0,.35)}
.hero-phone{left:484px;top:437px;width:232px;height:52px;border-radius:26px;background:var(--red);display:flex;align-items:center;padding-left:6px;color:var(--white);font-family:"Montserrat",sans-serif;font-weight:700;font-size:23px;letter-spacing:2px}
.hero-phone .ico{width:40px;height:40px;border-radius:50%;background:var(--white);display:flex;align-items:center;justify-content:center;margin-right:14px}
.dots{left:558px;top:694px;display:flex;gap:10px}
.dots span{width:13px;height:13px;border-radius:50%;background:var(--white)}
.dots span.on{box-shadow:0 0 0 3px rgba(255,255,255,.5);border:2px solid var(--navy)}

/* welcome */
.welcome-bg{left:0;top:600px;width:1200px;height:726px;background:linear-gradient(90deg,#e4e6e9 0%,#eceef0 100%);z-index:-1}
.welcome-photo{left:0;top:600px;width:560px;height:726px;background:linear-gradient(100deg,#2b4f96 0%,#3d65ad 35%,#c9ccd0 75%,rgba(236,238,240,0) 100%);z-index:-1}
.welcome{left:561px;top:872px;width:500px}
.h2{font-family:"Montserrat",sans-serif;font-size:38px;line-height:46px;color:var(--ink);font-weight:500}
.h2 .accent{color:var(--blue)}
.rule{width:52px;height:4px;background:var(--blue);margin-top:22px}
.welcome p{margin-top:34px;font-size:14.5px;line-height:32px;color:#555}
.btn-outline{display:inline-block;margin-top:28px;border:2px solid #333;padding:9px 27px;font-family:"Nunito Sans",sans-serif;font-weight:700;font-size:14px;color:#222}

/* services */
.svc{top:1326px;width:600px;height:424px;color:var(--white)}
.svc.red{left:0;background:var(--red-deep)}
.svc.blue{left:598px;width:602px;background:var(--blue-mid)}
.svc-inner{position:absolute;top:55px}
.svc-head{display:flex;align-items:center;gap:18px}
.svc-ico{width:82px;height:85px}
.svc-title{font-family:"Montserrat",sans-serif;font-weight:700;font-size:24px;line-height:34px;letter-spacing:.5px}
.svc p{margin-top:26px;width:400px;font-size:14px;line-height:28.6px}
.svc .mini{width:37px;height:3px;background:var(--white);margin-top:28px}
.svc .more{margin-top:12px;font-family:"Nunito Sans",sans-serif;font-weight:700;font-size:15px}

/* projects */
.projects{left:0;top:1680px;width:1200px;height:716px;background:var(--black);clip-path:polygon(0 70px,600px 0,1200px 70px,1200px 646px,600px 716px,0 646px)}
.proj-head{left:0;width:1200px;top:1780px;text-align:center;font-family:"Montserrat",sans-serif;font-size:38px;color:var(--white);font-weight:400}
.proj-head b{font-weight:700}
.rule-w{left:574px;top:1861px;width:52px;height:4px;background:var(--white)}
.card{top:1923px;width:298px;height:309px;overflow:hidden}
.card .ph{width:100%;height:100%}
.card .cap{position:absolute;left:0;bottom:0;width:100%;height:69px;background:rgba(240,74,80,.88);color:var(--white);text-align:center;font-family:"Nunito Sans",sans-serif;font-weight:700;font-size:18px;line-height:23px;padding-top:12px}
.card-feature{left:463px;top:2082px;width:298px;height:185px;background:rgba(50,102,180,.93);color:var(--white);text-align:center;font-family:"Nunito Sans",sans-serif}
.card-feature .t{font-weight:700;font-size:18px;line-height:24px;margin-top:38px}
.card-feature p{font-size:14px;line-height:24px;margin-top:6px;padding:0 12px}

/* why */
.why-bg{left:0;top:2326px;width:1200px;height:760px;background:linear-gradient(180deg,#f6f7f9,#eceef1);z-index:-1}
.why-head{left:0;width:1200px;top:2477px;text-align:center;font-family:"Montserrat",sans-serif;font-size:38px;color:var(--ink)}
.why-head b{font-weight:700}
.rule-b{height:4px;width:52px;background:var(--blue)}
.feat{width:440px;display:flex;gap:26px}
.feat .ic{flex:0 0 94px;height:94px;border:3px solid var(--blue-mid);border-radius:50%;display:flex;align-items:center;justify-content:center;background:var(--white)}
.feat h3{font-family:"Roboto",sans-serif;font-weight:500;font-size:18px;color:#333;margin-top:0}
.feat p{font-size:13.5px;line-height:24px;color:#666;margin-top:10px}

/* testimonials */
.testi{left:0;top:3013px;width:1200px;height:651px;background:var(--navy);clip-path:polygon(0 70px,600px 0,1200px 70px,1200px 583px,600px 651px,0 583px)}
.testi-head{left:0;width:1200px;top:3135px;text-align:center;font-family:"Montserrat",sans-serif;font-size:38px;color:var(--white);font-weight:300}
.testi-head b{font-weight:700}
.quote{top:3288px;width:405px;height:219px;background:var(--white);border-radius:4px;padding:40px 26px 0 26px}
.quote .qm{position:absolute;left:5px;top:-14px;width:44px;height:44px;border-radius:50%;background:var(--navy);border:3px solid var(--white);display:flex;align-items:center;justify-content:center;color:var(--white);font-family:"Montserrat",sans-serif;font-weight:700;font-size:30px;line-height:1}
.quote p{font-size:13.5px;line-height:26px;color:#444}
.quote .who{margin-top:12px;font-size:13.5px;line-height:25px;color:var(--blue)}
.quote .stars{position:absolute;right:44px;bottom:30px;color:var(--red);font-size:14px;letter-spacing:2px}

/* news */
.news-head{left:0;width:1200px;top:3728px;text-align:center;font-family:"Roboto",sans-serif;font-weight:700;font-size:38px;color:#2a2a2a}
.post{top:3855px;width:293px}
.post .ph{height:215px}
.post .body{margin-left:14px;border-left:2px solid #3a3a3a;padding-left:12px;margin-top:22px;padding-bottom:8px}
.post .date{font-size:14px;color:var(--red);display:flex;align-items:center;gap:8px}
.post p{font-size:12.5px;line-height:22px;color:#333;margin-top:10px}

/* footer */
.footer{left:0;top:4283px;width:1200px;height:471px;background:var(--black);clip-path:polygon(0 175px,600px 0,1200px 175px,1200px 471px,0 471px)}
.footer-edge{left:0;top:4280px}
.foot-head{left:0;width:1200px;top:4370px;text-align:center;font-family:"Montserrat",sans-serif;font-size:38px;color:var(--white)}
.foot-head b{font-weight:700}
.contact-row{left:0;width:1200px;top:4492px;display:flex;justify-content:center;gap:42px;color:var(--white);font-size:16px}
.contact-row span{display:flex;align-items:center;gap:12px}
.foot-links{left:0;width:1200px;top:4540px;text-align:center;color:var(--white);font-size:16px;word-spacing:3px}
.copy{left:0;width:1200px;top:4588px;text-align:center;color:var(--white);font-size:16px}
.social{left:536px;top:4639px;display:flex;gap:11px}
.social span{width:40px;height:40px;border-radius:50%;border:1.5px solid var(--blue)}
</style>
</head>
<body>

<!-- Hero -->
<div class="abs hero" role="img" aria-label="Photo of a technician in a hard hat servicing outdoor air conditioning units"></div>
<div class="abs hero-shade"></div>
<svg class="abs hero-edge" width="1200" height="175" viewBox="0 0 1200 175"><polyline points="0,4 600,170 1200,4" fill="none" stroke="#2f63ad" stroke-width="6"/></svg>
<div class="abs logo">Tolvar</div>
<nav class="abs nav"><a>HOME</a><a>ABOUT US</a><a>OUR SERVICES</a><a>BLOG</a><a>CONTACT US</a></nav>
<div class="abs hero-title"><div class="l1">AIR CONDITIONING</div><div class="l2">CONTRACTING</div></div>
<a class="abs hero-phone"><span class="ico"><svg width="20" height="20" viewBox="0 0 24 24"><path fill="#f04a50" d="M6.6 10.8a15.1 15.1 0 0 0 6.6 6.6l2.2-2.2c.3-.3.7-.4 1-.2 1.1.4 2.3.6 3.6.6.6 0 1 .4 1 1V20c0 .6-.4 1-1 1A17 17 0 0 1 3 4c0-.6.4-1 1-1h3.5c.6 0 1 .4 1 1 0 1.3.2 2.5.6 3.6.1.3 0 .7-.2 1z"/></svg></span>0417385926</a>
<div class="abs dots"><span class="on"></span><span></span><span></span><span></span></div>

<!-- Welcome -->
<div class="abs welcome-bg"></div>
<div class="abs welcome-photo" role="img" aria-label="Photo of two electricians in blue overalls and hard hats working on wiring"></div>
<section class="abs welcome">
  <h2 class="h2">WELCOME TO <span class="accent">TOLVAR</span></h2>
  <div class="rule"></div>
  <p>Sed ut perspiciatis unde omnis iste natus error sit voluptatem accusantium doloremque laudantium, totam rem aperiam, eaque ipsa quae ab illo inventore veritatis et quasi architecto beatae vitae dicta sunt explicabo. Nemo enim ipsam voluptatem quia voluptas sit aspernatur aut odit aut fugit, sed quia consequuntur magni dolores eos qui ratione voluptatem sequi nesciunt. Neque porro quisquam</p>
  <a class="btn-outline">READ MORE</a>
</section>

<!-- Services -->
<div class="abs svc red">
  <div class="svc-inner" style="left:144px">
    <div class="svc-head">
      <svg class="svc-ico" viewBox="0 0 82 85"><path d="M14 22A38 38 0 0 1 70 20M74 56A38 38 0 0 1 12 62" fill="none" stroke="#fff" stroke-width="4"/><circle cx="41" cy="42" r="18" fill="none" stroke="#fff" stroke-width="3"/><path d="M35 33v8M47 33v8M32 41h18v4a9 9 0 0 1-18 0zM41 54v6" fill="none" stroke="#fff" stroke-width="3"/></svg>
      <div class="svc-title">ELECTRICAL<br>CONTRACTING</div>
    </div>
    <p>Sed ut perspiciatis unde omnis iste natus error sit voluptatem accusantium doloremque laudantium, totam rem aperiam, eaque ipsa quae ab illo inventore veritatis et quasi architecto beatae vitae dicta sunt explicabo.</p>
    <div class="mini"></div><div class="more">READ MORE</div>
  </div>
</div>
<div class="abs svc blue">
  <div class="svc-inner" style="left:57px">
    <div class="svc-head">
      <svg class="svc-ico" viewBox="0 0 82 85"><path d="M14 22A38 38 0 0 1 70 20M74 56A38 38 0 0 1 12 62" fill="none" stroke="#fff" stroke-width="4"/><rect x="24" y="30" width="36" height="18" rx="2" fill="none" stroke="#fff" stroke-width="3"/><path d="M28 42h28M30 54c2 3 0 5 2 8M38 54c2 3 0 5 2 8M46 54c2 3 0 5 2 8" fill="none" stroke="#fff" stroke-width="2.5"/></svg>
      <div class="svc-title">AIR CONDITIONING<br>CONTRACTING</div>
    </div>
    <p>Sed ut perspiciatis unde omnis iste natus error sit voluptatem accusantium doloremque laudantium, totam rem aperiam, eaque ipsa quae ab illo inventore veritatis et quasi architecto beatae vitae dicta sunt explicabo.</p>
    <div class="mini"></div><div class="more">READ MORE</div>
  </div>
</div>

<!-- Projects -->
<div class="abs projects"></div>
<h2 class="abs proj-head"><b>OUR</b> PROJECTS</h2>
<div class="abs rule-w"></div>
<div class="abs card" style="left:150px"><div class="ph" role="img" aria-label="Photo of a wall-mounted split system air conditioner blowing cool air" style="background:linear-gradient(160deg,#dfe8ee,#9fb7c6)"></div><div class="cap">Air Conditioning<br>Contracting</div></div>
<div class="abs card" style="left:463px"><div class="ph" role="img" aria-label="Photo of an electrician working on a switchboard" style="background:linear-gradient(160deg,#6b7c93,#2f4f8a)"></div></div>
<div class="abs card-feature">
  <svg width="28" height="34" viewBox="0 0 28 34" style="position:absolute;left:135px;top:-2px"><rect x="3" y="2" width="22" height="30" fill="none" stroke="#fff" stroke-width="2.5"/><path d="M9 8h3M16 8h3M9 14h3M16 14h3M9 20h3M16 20h3M12 26h4v6h-4z" stroke="#fff" stroke-width="2.5"/></svg>
  <div class="t">Commercial<br>Electrical Services</div>
  <p>Sed ut perspiciatis unde omnis iste natus error sit voluptatem accusantium doloremque laudantium</p>
</div>
<div class="abs card" style="left:777px"><div class="ph" role="img" aria-label="Photo of a technician using a laptop beside industrial equipment" style="background:linear-gradient(160deg,#c9cdd1,#6f7780)"></div><div class="cap">Industrial<br>Electrical Services</div></div>

<!-- Why choose us -->
<div class="abs why-bg"></div>
<h2 class="abs why-head"><b>WHY</b> CHOOSE US?</h2>
<div class="abs rule-b" style="left:562px;top:2546px"></div>
<div class="abs feat" style="left:148px;top:2618px">
  <div class="ic"><svg width="50" height="50" viewBox="0 0 50 50"><circle cx="25" cy="25" r="21" fill="none" stroke="#2f63ad" stroke-width="3"/><path d="M20 14v8M30 14v8M16 22h18v5a9 9 0 0 1-18 0zM25 36v6" fill="none" stroke="#2f63ad" stroke-width="3"/></svg></div>
  <div><h3>Electrical Installations</h3><p>Sed ut perspiciatis unde omnis iste natus error sit voluptatem accusantium doloremque laudantium, totam rem aperiam, eaque ipsa quae ab illo inventore veritatis et quasi architecto</p></div>
</div>
<div class="abs feat" style="left:648px;top:2618px">
  <div class="ic"><svg width="50" height="44" viewBox="0 0 50 44"><rect x="3" y="4" width="44" height="30" rx="2" fill="none" stroke="#2f63ad" stroke-width="3"/><path d="M9 12h32M9 18h14M27 18h14M9 24h32M18 40h14" stroke="#2f63ad" stroke-width="3"/></svg></div>
  <div><h3>Air Conditioning Repair</h3><p>Sed ut perspiciatis unde omnis iste natus error sit voluptatem accusantium doloremque laudantium, totam rem aperiam, eaque ipsa quae ab illo inventore veritatis et quasi architecto</p></div>
</div>
<div class="abs feat" style="left:148px;top:2784px">
  <div class="ic"><svg width="46" height="46" viewBox="0 0 46 46"><path d="M8 8l30 30M38 8L8 38" stroke="#2f63ad" stroke-width="5" stroke-linecap="round"/><circle cx="8" cy="8" r="5" fill="none" stroke="#2f63ad" stroke-width="3"/><circle cx="38" cy="8" r="5" fill="none" stroke="#2f63ad" stroke-width="3"/></svg></div>
  <div><h3>Maintenance</h3><p>Sed ut perspiciatis unde omnis iste natus error sit voluptatem accusantium doloremque laudantium, totam rem aperiam, eaque ipsa quae ab illo inventore veritatis et quasi architecto</p></div>
</div>
<div class="abs feat" style="left:648px;top:2784px">
  <div class="ic"><svg width="46" height="46" viewBox="0 0 46 46"><path d="M10 18a13 13 0 0 1 26 0zM7 18h32" fill="#2f63ad" stroke="#2f63ad" stroke-width="3"/><path d="M6 44v-6a10 10 0 0 1 10-10h14a10 10 0 0 1 10 10v6z" fill="#2f63ad"/><circle cx="34" cy="34" r="7" fill="#fff" stroke="#2f63ad" stroke-width="3"/></svg></div>
  <div><h3>Electrical Contracting</h3><p>Sed ut perspiciatis unde omnis iste natus error sit voluptatem accusantium doloremque laudantium, totam rem aperiam, eaque ipsa quae ab illo inventore veritatis et quasi architecto</p></div>
</div>

<!-- Testimonials -->
<div class="abs testi"></div>
<h2 class="abs testi-head"><b>WHAT</b> OUR CUSTOMERS <b>ARE SAYING</b></h2>
<div class="abs rule-w" style="top:3214px"></div>
<div class="abs quote" style="left:162px">
  <div class="qm">&#8221;</div>
  <p>Sed ut perspiciatis unde omnis iste natus error sit voluptatem accusantium doloremque laudantium, totam rem aperiam, eaque ipsa quae ab illo inventore veritatis et quasi architecto beatae vitae</p>
  <div class="who">Dana Morrow<br>Tolvar</div>
  <div class="stars">☆☆☆☆☆</div>
</div>
<div class="abs quote" style="left:635px">
  <div class="qm">&#8221;</div>
  <p>Sed ut perspiciatis unde omnis iste natus error sit voluptatem accusantium doloremque laudantium, totam rem aperiam, eaque ipsa quae ab illo inventore veritatis et quasi architecto beatae vitae</p>
  <div class="who">Dana Morrow<br>Tolvar</div>
  <div class="stars">☆☆☆☆☆</div>
</div>

<!-- News -->
<h2 class="abs news-head">LATEST NEWS</h2>
<div class="abs rule-b" style="left:561px;top:3794px"></div>
<article class="abs post" style="left:126px"><div class="ph" role="img" aria-label="Photo of outdoor air conditioning units beside a house" style="background:linear-gradient(170deg,#8a8b7d,#5e6a4e)"></div>
  <div class="body"><div class="date"><svg width="12" height="12" viewBox="0 0 12 12"><rect x="1" y="2" width="10" height="9" fill="#f04a50"/></svg>October 17, 2019</div><p>Lorem ipsum dolor sit amet, consectetur adipi scing elit, sed do eiusmod tempor incididunt ut labore et dolore magna aliqua Ut enim ad minim veniam</p></div></article>
<article class="abs post" style="left:447px"><div class="ph" role="img" aria-label="Photo of an electrician in a white hard hat at a switchboard" style="background:linear-gradient(170deg,#b5b8bc,#3f4650)"></div>
  <div class="body"><div class="date"><svg width="12" height="12" viewBox="0 0 12 12"><rect x="1" y="2" width="10" height="9" fill="#f04a50"/></svg>October 17, 2019</div><p>Lorem ipsum dolor sit amet, consectetur adipi scing elit, sed do eiusmod tempor incididunt ut labore et dolore magna aliqua Ut enim ad minim veniam</p></div></article>
<article class="abs post" style="left:768px"><div class="ph" role="img" aria-label="Photo of an electrician fitting a ceiling light" style="background:linear-gradient(170deg,#c5c9cf,#3d5a93)"></div>
  <div class="body"><div class="date"><svg width="12" height="12" viewBox="0 0 12 12"><rect x="1" y="2" width="10" height="9" fill="#f04a50"/></svg>October 17, 2019</div><p>Lorem ipsum dolor sit amet, consectetur adipi scing elit, sed do eiusmod tempor incididunt ut labore et dolore magna aliqua Ut enim ad minim veniam</p></div></article>

<!-- Footer -->
<footer>
<div class="abs footer"></div>
<svg class="abs footer-edge" width="1200" height="182" viewBox="0 0 1200 182"><polyline points="0,178 600,3 1200,178" fill="none" stroke="#2f63ad" stroke-width="5"/></svg>
<h2 class="abs foot-head"><b>CONTACT</b> US</h2>
<div class="abs contact-row">
  <span><svg width="11" height="15" viewBox="0 0 11 15"><path d="M5.5 0A5.5 5.5 0 0 0 0 5.5C0 9.5 5.5 15 5.5 15S11 9.5 11 5.5A5.5 5.5 0 0 0 5.5 0zm0 7.5a2 2 0 1 1 0-4 2 2 0 0 1 0 4z" fill="#33a6d7"/></svg>Tolvar, Corvale, WA, 6027</span>
  <span><svg width="14" height="14" viewBox="0 0 24 24"><path fill="#33a6d7" d="M6.6 10.8a15.1 15.1 0 0 0 6.6 6.6l2.2-2.2c.3-.3.7-.4 1-.2 1.1.4 2.3.6 3.6.6.6 0 1 .4 1 1V20c0 .6-.4 1-1 1A17 17 0 0 1 3 4c0-.6.4-1 1-1h3.5c.6 0 1 .4 1 1 0 1.3.2 2.5.6 3.6.1.3 0 .7-.2 1z"/></svg>0417385926</span>
  <span><svg width="15" height="11" viewBox="0 0 15 11"><rect width="15" height="11" rx="1" fill="#33a6d7"/><path d="M0 1l7.5 5L15 1" fill="none" stroke="#161616" stroke-width="1.3"/></svg>info@tolvar.com.au</span>
</div>
<div class="abs foot-links">Home &nbsp;|&nbsp; About us &nbsp;|&nbsp; Our Services &nbsp;|&nbsp; Blog &nbsp;|&nbsp; Contact Us</div>
<div class="abs copy">© 2019 Tolvar. All Rights Reserved.</div>
<div class="abs social"><span></span><span></span><span></span></div>
</footer>

</body>
</html>
```